Create a Dynamic Website for Roadhaven 41Ter!

Dear designers,
We have an exciting design opportunity for you on PixelBazaar. We are in need of a creative and professional website design for our company, Roadhaven 41Ter. Our current website is outdated and fails to convey the image we want to project. We are determined to revamp our online presence and create a website that truly represents who we are.
Roadhaven 41Ter is a versatile establishment offering a Velko Express, sandwich bar, restaurant, parking facilities, and meeting rooms. Each of these aspects deserves its own spotlight on our website. Therefore, we are seeking a WordPress-based website design that allows us to easily make changes, modify texts, and add new content as needed.
It is crucial that the design aligns seamlessly with our new branding and style. We invite you to explore our Photoline (@Roadhaven41ter) and Facebook (@Roadhaven) pages to gain an understanding of our branding and incorporate those elements into the design.
You can find our current website at www.guardedroadhaven.eu, but we want a new website that is vibrant, dynamic, and includes moving elements if possible. We believe this will enhance the user experience and keep visitors engaged for longer periods.
Key elements we would like to include in the new website design are as follows:
Clear presentation of all our services: Velko Express, sandwich bar, restaurant, parking facilities, and meeting rooms.
Easy navigation for visitors to find information effortlessly.
Engaging call-to-action buttons that encourage visitors to take specific actions, such as reserving a meeting room or placing an order.
A dedicated blog section where we can share news, events, and special offers.
Integration of a contact form and contact details for easy communication with our visitors.
Responsive design that works seamlessly across desktop and mobile devices.
We envision a modern and visually appealing website that leaves a lasting positive impression on visitors. We are interested in a design that incorporates creative visual elements and provides a user-friendly interface.
Thank you for your time, and we eagerly await your designs.
Best regards,

```html
<!DOCTYPE html>
<html lang="en">
<head>
<meta charset="utf-8">
<title>Roadhaven 41Ter</title>
<link rel="stylesheet" href="https://fonts.googleapis.com/css2?family=Rubik:wght@400;500;600;700&family=Roboto:wght@400;500;700&display=swap">
<style>
:root{
  --navy:#262a5e;
  --navy-deep:#23265a;
  --red:#d7191f;
  --blue:#1e78c2;
  --ink:#222;
  --muted:#666;
  --line:#c9c9c9;
  --white:#fff;
}
*{box-sizing:border-box;margin:0;padding:0}
html,body{width:1200px;height:4769px;overflow:hidden}
body{font-family:"Roboto",Arial,sans-serif;color:var(--ink);background:var(--white);position:relative}
.abs{position:absolute}
h1,h2,h3,.brand{font-family:"Rubik",Arial,sans-serif}
.btn-red{position:absolute;background:var(--red);color:#fff;font-family:"Rubik",sans-serif;font-weight:600;font-size:13px;display:flex;align-items:center;justify-content:center;text-transform:uppercase;letter-spacing:.2px}
.circle-arrow{position:absolute;width:40px;height:40px;border-radius:50%;background:#e7e7e7;display:flex;align-items:center;justify-content:center;border:1px solid #d0d0d0}
.photo{position:absolute}
.section-title{position:absolute;left:0;width:1200px;text-align:center;font-family:"Rubik",sans-serif;font-weight:600;font-size:37px;color:var(--navy)}

/* header */
.site-header{position:absolute;top:0;left:0;width:1200px;height:113px;background:#fff}
.brand{position:absolute;left:115px;top:34px;display:flex;align-items:center;gap:10px;font-weight:700;font-size:24px;color:var(--navy)}
.brand .mark{width:18px;height:18px;background:var(--red)}
.call{position:absolute;left:844px;top:22px;display:flex;align-items:center;gap:10px;font-size:12px;color:#333}
.call b{font-family:"Rubik",sans-serif;font-size:19px;font-weight:500;color:#222}
.call .ico{width:30px;height:30px;border-radius:50%;background:var(--blue);display:flex;align-items:center;justify-content:center}
.main-nav{position:absolute;left:387px;top:74px;display:flex;gap:21px;font-family:"Rubik",sans-serif;font-weight:500;font-size:13px;color:#222}
.main-nav .active{color:var(--red)}

/* hero */
.hero{position:absolute;top:113px;left:0;width:1200px;height:600px;background:linear-gradient(110deg,#2b2320 0%,#5a4236 30%,#8d6b4d 52%,#4e3e33 75%,#221c1a 100%)}
.hero .tag{position:absolute;left:550px;top:366px;width:100px;height:34px;background:var(--blue);color:#fff;font-family:"Rubik",sans-serif;font-weight:600;font-size:15px;display:flex;align-items:center;justify-content:center}
.hero h1{position:absolute;left:0;top:406px;width:1200px;text-align:center;color:#fff;font-weight:700;font-size:50px;letter-spacing:.5px}
.hero .btn-red{left:474px;top:492px;width:254px;height:42px}

/* about */
.about-frame{position:absolute;left:94px;top:798px;width:150px;height:409px;border:17px solid var(--red);border-right:none}
.about-photo{left:111px;top:817px;width:489px;height:370px;background:linear-gradient(160deg,#cfd4dc 0%,#9ea6b3 45%,#5e6677 75%,#a33a3c 100%)}
.about-text{position:absolute;left:635px;top:808px;width:445px}
.about-text h2{font-size:38px;font-weight:700;color:var(--navy)}
.about-text h3{font-size:17px;font-weight:600;color:var(--red);margin-top:4px}
.about-text p{font-size:13px;line-height:25.5px;color:#555;margin-top:16px;text-align:justify}
.about .btn-red{left:636px;top:1146px;width:152px;height:41px}

/* services */
.service-card{position:absolute;top:1376px;width:285px;height:404px}
.service-card .label{position:absolute;left:50%;transform:translateX(-50%);top:318px;height:47px;padding:0 22px;background:var(--blue);color:#fff;font-family:"Rubik",sans-serif;font-weight:600;font-size:18px;display:flex;align-items:center;white-space:nowrap}

/* meetings */
.meetings{position:absolute;top:1796px;left:0;width:1200px;height:432px;background:linear-gradient(180deg,rgba(38,42,94,.88),rgba(38,42,94,.92)),linear-gradient(90deg,#6c7284,#3f4560 50%,#5b6275)}
.meetings h2{position:absolute;top:100px;left:0;width:1200px;text-align:center;color:#fff;font-size:38px;font-weight:600}
.meetings .copy{position:absolute;top:168px;left:190px;width:820px;text-align:center;color:#fff;font-size:13px;line-height:21px}
.meetings .copy p+p{margin-top:22px}

/* events */
.event{position:absolute}
.event .img{position:absolute;left:0;top:0;border-radius:10px}
.event .card{position:absolute;background:#fff;border:1px solid #ddd;border-radius:10px;text-align:center;padding:24px 20px 0}
.event h3{font-family:"Roboto",sans-serif;font-weight:500;font-size:25px;line-height:34px;color:#222}
.event p{font-size:13px;line-height:21px;color:#777;margin-top:12px}
.event .more{margin-top:12px;font-family:"Rubik",sans-serif;font-size:13px;font-weight:600;color:var(--red);display:flex;justify-content:center;align-items:center;gap:4px}
.event .bar{position:absolute;bottom:0;left:50%;transform:translateX(-50%);width:118px;height:4px;background:var(--blue)}

/* news */
.news{position:absolute;top:2937px;left:0;width:1200px;height:826px;background:var(--blue)}
.news h2{position:absolute;top:82px;width:1200px;text-align:center;color:#fff;font-size:35px;font-weight:600}
.news-box{position:absolute;background:#fff;padding:16px 26px}
.news-meta{display:flex;gap:28px;font-family:"Rubik",sans-serif;font-size:12px;color:#222;align-items:center}
.news-meta span{display:flex;align-items:center;gap:5px}
.news-box h3{font-size:19px;font-weight:500;color:var(--navy);margin-top:9px}
.news-box p{font-size:13px;line-height:23px;color:#666;margin-top:6px}
.news .btn-red{left:511px;top:709px;width:176px;height:39px;font-size:12px}

/* contact */
.field{position:absolute;border:1px solid var(--line);background:#fff;font-size:13px;color:#777;padding:20px 28px}
.contact .btn-red{left:480px;top:4210px;width:244px;height:55px}

/* footer */
.site-footer{position:absolute;top:4371px;left:0;width:1200px;height:398px;background:var(--navy-deep);color:#fff}
.site-footer .brand{left:122px;top:145px;color:#fff;font-size:28px}
.foot-col{position:absolute;top:100px}
.foot-col h4{font-family:"Rubik",sans-serif;font-weight:500;font-size:19px}
.foot-col ul{list-style:none;margin-top:14px}
.foot-col li{font-size:13px;line-height:26px;display:flex;align-items:center;gap:14px}
.foot-col .dot{width:11px;height:11px;background:#fff;display:inline-block}
.copyright{position:absolute;top:327px;width:1200px;text-align:center;font-size:12px}
</style>
</head>
<body>

<header class="site-header">
  <div class="brand"><span class="mark"></span>ROADHAVEN 41TER</div>
  <a class="btn-red" style="left:606px;top:18px;width:194px;height:39px">Placing an order</a>
  <div class="call">
    <span class="ico"><svg width="14" height="14" viewBox="0 0 24 24"><path fill="#fff" d="M6.6 10.8a15 15 0 0 0 6.6 6.6l2.2-2.2c.3-.3.7-.4 1-.2 1.1.4 2.3.6 3.6.6.6 0 1 .4 1 1V20c0 .6-.4 1-1 1A17 17 0 0 1 3 4c0-.6.4-1 1-1h3.5c.6 0 1 .4 1 1 0 1.3.2 2.5.6 3.6.1.3 0 .7-.2 1z"/></svg></span>
    <span>Call Us Today : <b>013 555 0148</b></span>
  </div>
  <nav class="main-nav">
    <span class="active">HOME</span><span>OVER ONS</span><span>BROODJESBAR</span><span>RESTAURANT</span><span>PARKING</span><span>SEMINARIES // FEESTZAAL</span><span>MORE ▾</span>
  </nav>
</header>

<section class="hero" role="img" aria-label="Guests sharing sandwiches at the food counter under string lights">
  <div class="circle-arrow" style="left:111px;top:278px"><svg width="10" height="10" viewBox="0 0 10 10"><path d="M7 1 3 5l4 4" stroke="#444" stroke-width="1.5" fill="none"/></svg></div>
  <div class="circle-arrow" style="left:1047px;top:278px"><svg width="10" height="10" viewBox="0 0 10 10"><path d="M3 1l4 4-4 4" stroke="#444" stroke-width="1.5" fill="none"/></svg></div>
  <div class="tag">SECURE</div>
  <h1>ROADHAVEN41TER</h1>
  <a class="btn-red">Reserving a meeting room</a>
</section>

<section class="about">
  <div class="about-frame"></div>
  <div class="photo about-photo" role="img" aria-label="Front of the café and restaurant building"></div>
  <div class="about-text">
    <h2>ABOUT US</h2>
    <h3>SO MUCH MORE THAN A TRUCKSTOP.</h3>
    <p>Roadhaven41Ter was founded in 2009 thanks to four partners, with a strong vision of safety and comfort for truck drivers. In 2020, it is the Varden brothers who continue this vision.</p>
    <p style="margin-top:26px">Transport is therefore indispensable in our current society.<br>The Varden brothers, themselves active in the transport world, know where the pain points lie in the sector. That is why they strive with Roadhaven41Ter to offer a solution to the problems of safety, comfort, hygiene, parking and decent healthy meals.</p>
  </div>
  <a class="btn-red">Learn more</a>
</section>

<section class="services">
  <h2 class="section-title" style="top:1282px">OUR SERVICES</h2>
  <div class="circle-arrow" style="left:113px;top:1292px"><svg width="10" height="10" viewBox="0 0 10 10"><path d="M7 1 3 5l4 4" stroke="#444" stroke-width="1.5" fill="none"/></svg></div>
  <div class="circle-arrow" style="left:1047px;top:1292px"><svg width="10" height="10" viewBox="0 0 10 10"><path d="M3 1l4 4-4 4" stroke="#444" stroke-width="1.5" fill="none"/></svg></div>
  <div class="service-card" style="left:0;background:linear-gradient(160deg,#cfd4dc,#8b93a3 60%,#a33a3c)" role="img" aria-label="Velko Express shop front"><span class="label">VELKO EXPRESS</span></div>
  <div class="service-card" style="left:305px;background:linear-gradient(170deg,#2a2a2a,#6b4a33 55%,#3a2c24)" role="img" aria-label="Sandwich bar counter with guests"><span class="label">SANDWICH BAR</span></div>
  <div class="service-card" style="left:610px;background:linear-gradient(170deg,#3b4356,#b98a4c 50%,#4a3a2e)" role="img" aria-label="Restaurant dining room with pendant lamps"><span class="label">RESTAURANT</span></div>
  <div class="service-card" style="left:915px;background:linear-gradient(170deg,#b7c7cf,#8d969c 55%,#4f5458)" role="img" aria-label="Row of parked cars"><span class="label">PARKING FACILITIES</span></div>
</section>

<section class="meetings">
  <h2>MEETINGS AT ROADHAVEN 41TER</h2>
  <div class="copy">
    <p>Are you still looking for a meeting room? Then Roadhaven41Ter is the perfect location. We have 4 meeting rooms with a maximum capacity of 70p. Beamer, wifi, whiteboard are all present.</p>
    <p>We provide a full drinks package with all types of soft drinks, water &amp; coffee. During the lunch break we also offer you different packages, a sandwich or a cup of soup or even a full menu!</p>
    <p>If you are interested in this, you can always call: + 32 13 555 0192</p>
  </div>
</section>

<section class="events">
  <h2 class="section-title" style="top:2322px;color:#222">OUR EVENTS</h2>
  <svg class="abs" style="left:36px;top:2650px" width="14" height="22" viewBox="0 0 14 22"><path d="M11 2 3 11l8 9" stroke="#222" stroke-width="2" fill="none"/></svg>
  <svg class="abs" style="left:1136px;top:2650px" width="14" height="22" viewBox="0 0 14 22"><path d="M3 2l8 9-8 9" stroke="#222" stroke-width="2" fill="none"/></svg>

  <div class="event" style="left:93px;top:2402px;width:309px;height:441px">
    <div class="img" style="width:309px;height:265px;background:linear-gradient(170deg,#c9b9a2,#8a5a3e 55%,#6c3d4a)" role="img" aria-label="Restaurant interior with tables and chairs"></div>
    <div class="card" style="left:13px;top:215px;width:283px;height:226px">
      <h3>Nemo enim ipsam voluptatem</h3>
      <p>Lorem ipsum dolor sit amet, consec tetur adipiscing elit, sed do eiusmod tempor incididunt</p>
      <div class="more">READ MORE <svg width="11" height="11" viewBox="0 0 12 12"><circle cx="6" cy="6" r="6" fill="#d7191f"/><path d="M5 3.5 7.5 6 5 8.5" stroke="#fff" stroke-width="1.5" fill="none"/></svg></div>
      <span class="bar"></span>
    </div>
  </div>

  <div class="event" style="left:424px;top:2385px;width:350px;height:458px">
    <div class="img" style="width:350px;height:292px;background:linear-gradient(170deg,#e4e4e4,#9b5a40 45%,#6b6b6b)" role="img" aria-label="Dining hall with a brick fireplace"></div>
    <div class="card" style="left:32px;top:232px;width:287px;height:226px">
      <h3>Nemo enim ipsam voluptatem</h3>
      <p>Lorem ipsum dolor sit amet, consec tetur adipiscing elit, sed do eiusmod tempor incididunt</p>
      <div class="more">READ MORE <svg width="11" height="11" viewBox="0 0 12 12"><circle cx="6" cy="6" r="6" fill="#d7191f"/><path d="M5 3.5 7.5 6 5 8.5" stroke="#fff" stroke-width="1.5" fill="none"/></svg></div>
      <span class="bar"></span>
    </div>
  </div>

  <div class="event" style="left:795px;top:2402px;width:311px;height:441px">
    <div class="img" style="width:311px;height:265px;background:linear-gradient(170deg,#4d5b86,#d9d2c4 50%,#a58b6a)" role="img" aria-label="Meeting room set with tables in a U shape"></div>
    <div class="card" style="left:13px;top:215px;width:285px;height:226px">
      <h3>Nemo enim ipsam voluptatem</h3>
      <p>Lorem ipsum dolor sit amet, consec tetur adipiscing elit, sed do eiusmod tempor incididunt</p>
      <div class="more">READ MORE <svg width="11" height="11" viewBox="0 0 12 12"><circle cx="6" cy="6" r="6" fill="#d7191f"/><path d="M5 3.5 7.5 6 5 8.5" stroke="#fff" stroke-width="1.5" fill="none"/></svg></div>
      <span class="bar"></span>
    </div>
  </div>
</section>

<section class="news">
  <h2>LATEST NEWS</h2>
  <div class="photo" style="left:111px;top:150px;width:487px;height:533px;background:linear-gradient(160deg,#1f3b6e,#8a5b3c 45%,#3b2a22)" role="img" aria-label="Staff serving a sandwich to a customer"></div>
  <div class="news-box" style="left:135px;top:519px;width:439px;height:142px">
    <div class="news-meta"><span><svg width="10" height="11" viewBox="0 0 10 11"><circle cx="5" cy="3" r="2.6" fill="#d7191f"/><path d="M0 11c0-3 2-5 5-5s5 2 5 5z" fill="#d7191f"/></svg>John doe</span><span><svg width="11" height="11" viewBox="0 0 11 11"><rect x=".5" y="1.5" width="10" height="9" fill="none" stroke="#d7191f"/><rect x=".5" y="1.5" width="10" height="2.5" fill="#d7191f"/></svg>Jan 20,2023</span></div>
    <h3>LOREM IPSUM DOLOR SIT AMET</h3>
    <p>Lorem ipsum dolor sit amet, consectetur adipiscing elit, sed do tempor incididunt ut labore et dolore magna aliqua.</p>
  </div>

  <div class="photo" style="left:617px;top:150px;width:470px;height:256px;background:linear-gradient(160deg,#d9d6d0,#8c8d92 55%,#5e5e62)" role="img" aria-label="Conference room with white table and chairs"></div>
  <div class="news-box" style="left:820px;top:248px;width:252px;height:139px">
    <div class="news-meta"><span><svg width="10" height="11" viewBox="0 0 10 11"><circle cx="5" cy="3" r="2.6" fill="#d7191f"/><path d="M0 11c0-3 2-5 5-5s5 2 5 5z" fill="#d7191f"/></svg>John doe</span><span><svg width="11" height="11" viewBox="0 0 11 11"><rect x=".5" y="1.5" width="10" height="9" fill="none" stroke="#d7191f"/><rect x=".5" y="1.5" width="10" height="2.5" fill="#d7191f"/></svg>Jan 20,2023</span></div>
    <h3>LOREM IPSUM DOL</h3>
    <p>Lorem ipsum dolor sit amet, consectetur adipiscing elit, sed</p>
  </div>

  <div class="photo" style="left:617px;top:428px;width:470px;height:255px;background:linear-gradient(160deg,#8a8a86,#c9b48f 40%,#4a4034)" role="img" aria-label="Buffet trays with fresh dishes"></div>
  <div class="news-box" style="left:820px;top:526px;width:252px;height:139px">
    <div class="news-meta"><span><svg width="10" height="11" viewBox="0 0 10 11"><circle cx="5" cy="3" r="2.6" fill="#d7191f"/><path d="M0 11c0-3 2-5 5-5s5 2 5 5z" fill="#d7191f"/></svg>John doe</span><span><svg width="11" height="11" viewBox="0 0 11 11"><rect x=".5" y="1.5" width="10" height="9" fill="none" stroke="#d7191f"/><rect x=".5" y="1.5" width="10" height="2.5" fill="#d7191f"/></svg>Jan 20,2023</span></div>
    <h3>LOREM IPSUM DOL</h3>
    <p>Lorem ipsum dolor sit amet, consectetur adipiscing elit, sed</p>
  </div>

  <a class="btn-red">View more news</a>
</section>

<section class="contact">
  <h2 class="section-title" style="top:3885px;color:#222">CONTACT</h2>
  <div class="field" style="left:209px;top:3963px;width:247px;height:58px">Name</div>
  <div class="field" style="left:480px;top:3963px;width:244px;height:58px">Email</div>
  <div class="field" style="left:748px;top:3963px;width:247px;height:58px">Phone</div>
  <div class="field" style="left:209px;top:4048px;width:786px;height:136px">Message</div>
  <a class="btn-red">Submit now</a>
</section>

<footer class="site-footer">
  <div class="brand"><span class="mark"></span>ROADHAVEN 41TER</div>
  <div class="foot-col" style="left:467px">
    <h4>Quick Links</h4>
    <ul>
      <li><span>»</span>Home</li><li><span>»</span>About us</li><li><span>»</span>Services</li><li><span>»</span>Teams</li><li><span>»</span>Contact us</li>
    </ul>
  </div>
  <div class="foot-col" style="left:681px">
    <h4>Contact us</h4>
    <ul>
      <li><svg width="10" height="13" viewBox="0 0 10 13"><path d="M5 0a5 5 0 0 1 5 5c0 3.5-5 8-5 8S0 8.5 0 5a5 5 0 0 1 5-5z" fill="#d7191f"/><circle cx="5" cy="5" r="1.8" fill="#23265a"/></svg>Depot Lane 8</li>
      <li style="padding-left:24px">3500 Meerdonk</li>
      <li><svg width="11" height="11" viewBox="0 0 24 24"><path fill="#d7191f" d="M6.6 10.8a15 15 0 0 0 6.6 6.6l2.2-2.2c.3-.3.7-.4 1-.2 1.1.4 2.3.6 3.6.6.6 0 1 .4 1 1V20c0 .6-.4 1-1 1A17 17 0 0 1 3 4c0-.6.4-1 1-1h3.5c.6 0 1 .4 1 1 0 1.3.2 2.5.6 3.6.1.3 0 .7-.2 1z"/></svg>013 555 0148</li>
      <li>&nbsp;</li>
      <li><svg width="12" height="9" viewBox="0 0 12 9"><rect width="12" height="9" fill="#d7191f"/><path d="M0 0l6 5 6-5" stroke="#23265a" fill="none"/></svg>info@roadhaven41ter.eu</li>
    </ul>
  </div>
  <div class="foot-col" style="left:991px">
    <h4>Follow us</h4>
    <ul>
      <li><span class="dot"></span>Photoline</li>
      <li><span class="dot"></span>Worknet</li>
    </ul>
  </div>
  <div class="copyright">© Copyrights 2023 The Company Name | All Rights Reserved &nbsp;|&nbsp; Privacy Policy</div>
</footer>

</body>
</html>
```